Novexa company website, a website for employment for people with autism

The website will make a match between people and jobs, mainly in the graphical sector, but also other sectors.
The name of the company is novexa and automates jobs with people that are on the autism spectrum.
The whole matchmaking and feedback process and so doesn't have to be in this prototype, we just want the general information pages and to convey a great look and brand identity that we will keep in the other pages to be developed. The website must be made with Wordpress, since the backend will be developed in Wordpress too.
It is a social project that wants to create possibilites for people with ASS to work from home for an employer or to do a variety of tasks for different customers.
The people we hire are generally not on the regular job market or have difficulty finding a job and "selling themselves"

Target Market(s)

matchmaking between talent (with ASS) and employers / jobs

Number of Pages Required

5+ page

Font styles to use
Sans Serif

Colors
ec1f27
e34298
a64599
6b449b
0355a3
0792cd

Requirements
Must have
• A stunning landing pages
• Integrate our logo and must match with what will do. We want a clean, modern, minimalistic, sleek website that radiates creativity and good looks.
• We have one page describing what we can do for customers, one page for people with ASS that would like to be candidates (our approach, learning program, ...), two pages that are addressed to partners who want to cooperate: the one's that can assist with autism related assistance and the one's that can help with the job coaching.
Nice to have
• In our logo are many colors as we embrace diversity and want to show that. Out main branding colors are red (for action) and blue for stability and will all gradients that go with it. Mainly white or black (or anthracite) for other parts
Should not have
• We want a modern and minimalistic design, no fluffy designs with lots of ornaments.

```html
<!DOCTYPE html>
<html lang="en">
<head>
<meta charset="utf-8">
<title>Novexa – Autism Jobs</title>
<link href="https://fonts.googleapis.com/css2?family=Poppins:wght@400;600;700;800&family=Open+Sans:wght@400;600;700&display=swap" rel="stylesheet">
<style>
:root{
  --red:#ec1f27;
  --pink:#e34298;
  --violet:#a64599;
  --purple:#6b449b;
  --deep:#4a2a86;
  --blue:#0355a3;
  --sky:#0792cd;
  --ink:#1e1b24;
  --text:#4a4754;
  --soft:#f4f2f8;
  --grey:#f1f1f3;
  --white:#fff;
}
*{margin:0;padding:0;box-sizing:border-box}
html,body{width:1200px;height:4534px;overflow:hidden}
body{position:relative;background:var(--white);font-family:'Open Sans',sans-serif;color:var(--text)}
.abs{position:absolute}
h1,h2,h3,.brand,.btn,.nav a{font-family:'Poppins',sans-serif}
.btn{position:absolute;display:flex;align-items:center;justify-content:center;background:var(--purple);color:#fff;font-weight:700;text-transform:uppercase;font-size:16px;letter-spacing:.5px;text-decoration:none}
.btn.small{font-size:11px;height:26px;width:88px}
.section-title{position:absolute;left:0;width:1200px;text-align:center;font-size:36px;font-weight:800;color:var(--ink);letter-spacing:.5px}
.section-title::after{content:"";display:block;width:40px;height:3px;background:#aaa;margin:18px auto 0}

/* hero */
.hero-bg{left:0;top:0}
.brand{font-weight:600;color:#fff;letter-spacing:6px}
.header-brand{left:58px;top:105px;font-size:44px;display:flex;align-items:center;gap:14px}
.header-brand .dot{width:22px;height:22px;border-radius:50%;background:var(--pink)}
.nav{left:535px;top:34px;display:flex;gap:26px}
.nav a{color:#fff;font-size:13px;font-weight:700;text-decoration:none}
.call{left:1012px;top:22px;display:flex;gap:10px;align-items:center;color:#fff;font-family:'Poppins',sans-serif}
.call small{display:block;font-size:11px;font-weight:700}
.call b{font-size:17px;font-weight:700}
.hero-title{left:0;top:262px;width:1200px;text-align:center;color:#fff;font-size:60px;font-weight:800}
.hero-sub{left:0;top:342px;width:1200px;text-align:center;color:#fff;font-size:18px;font-weight:700}
.dots{left:538px;top:585px;display:flex;gap:14px}
.dots i{width:9px;height:9px;border-radius:50%;background:#d8d5e0;display:block}
.dots i.on{background:var(--pink)}

/* welcome */
.welcome-text{left:650px;top:758px;width:420px}
.welcome-text h3{font-size:28px;font-weight:600;color:var(--ink)}
.welcome-text h2{font-size:52px;font-weight:800;color:var(--ink);letter-spacing:2px;line-height:1.05}
.welcome-text p{font-size:15px;line-height:1.45;margin-top:26px;color:var(--text)}

/* services */
.service{position:absolute;top:1644px;width:200px;text-align:center}
.service h3{font-size:15px;font-weight:800;color:var(--ink)}
.service p{font-size:13px;line-height:1.5;margin-top:10px}

/* banner */
.banner-text{left:160px;top:2010px;width:470px;color:#fff}
.banner-text h2{font-size:34px;font-weight:800;line-height:1.25;text-transform:uppercase}
.banner-text p{font-size:19px;line-height:1.3;margin-top:26px}

/* jobs */
.job-card{left:640px;top:2555px;width:420px;height:455px;background:#fff;box-shadow:0 6px 28px rgba(40,20,80,.14);padding:60px 0 0 20px}
.tag{display:inline-block;border:2px solid #222;padding:6px 16px;font-family:'Poppins',sans-serif;font-size:13px;font-weight:800;color:var(--ink)}
.job-card h3{font-size:22px;font-weight:800;color:var(--ink);line-height:1.2;margin-top:22px;width:340px;text-transform:uppercase}
.job-card p{font-size:13.5px;line-height:1.45;margin-top:14px;width:330px}

/* blog */
.post{position:absolute;top:3295px;width:170px}
.post time{font-size:13px;color:var(--ink)}
.post h3{font-size:15px;font-weight:800;color:var(--ink);margin-top:8px;line-height:1.2;text-transform:uppercase}
.post p{font-size:13px;line-height:1.45;margin-top:12px}

/* testimonials */
.testimonials{left:0;top:3643px;width:1200px;height:510px;background:var(--grey)}
.quote{left:320px;top:3815px;width:560px;text-align:center;font-size:16px;line-height:1.45;color:var(--text)}
.qmark{font-family:'Poppins',sans-serif;font-size:80px;font-weight:800;color:var(--purple);line-height:1}
.author{left:0;top:4070px;width:1200px;text-align:center;font-family:'Poppins',sans-serif;font-weight:800;font-size:13px;color:var(--ink)}
.author::before{content:"";display:block;width:34px;height:2px;background:#888;margin:0 auto 16px}

/* footer */
.footer-col{position:absolute;top:4238px;color:#fff;font-size:12px}
.footer-col h4{font-family:'Poppins',sans-serif;font-size:13px;font-weight:800;margin-bottom:18px}
.footer-col li{list-style:none;line-height:1.5;display:flex;gap:12px;align-items:flex-start;margin-bottom:14px}
.menu li{margin-bottom:0}
.social li{align-items:center;margin-bottom:12px}
.social .ico{width:22px;height:22px;border-radius:50%;background:var(--sky);flex:none}
.copyright{left:0;top:4484px;width:1200px;text-align:center;color:#fff;font-size:12px}
</style>
</head>
<body>

<!-- HERO -->
<svg class="abs hero-bg" width="1200" height="620" viewBox="0 0 1200 620">
  <defs>
    <linearGradient id="sky" x1="0" y1="0" x2="0" y2="1">
      <stop offset="0" stop-color="#2f3d52"/>
      <stop offset=".5" stop-color="#6d7a8e"/>
      <stop offset="1" stop-color="#3a4658"/>
    </linearGradient>
  </defs>
  <path role="img" aria-label="Dramatic cloudy sky photograph" d="M0 0H1200V545L600 600 0 545Z" fill="url(#sky)"/>
  <path d="M0 545L600 600 1200 545" fill="none" stroke="var(--pink)" stroke-width="9"/>
</svg>
<div class="abs brand header-brand"><span class="dot"></span>NOVEXA</div>
<nav class="abs nav"><a href="#">HOME</a><a href="#">ABOUT US</a><a href="#">SERVICES</a><a href="#">JOBS</a><a href="#">BLOG</a><a href="#">CONTACT US</a></nav>
<div class="abs call">
  <svg width="28" height="28" viewBox="0 0 28 28"><circle cx="14" cy="14" r="14" fill="#fff"/><path d="M10 8l3 3-2 2a9 9 0 004 4l2-2 3 3-2 2c-5 0-11-6-11-11z" fill="var(--deep)"/></svg>
  <div><small>CALL US</small><b>888.888.8888</b></div>
</div>
<h1 class="abs hero-title">AUTISM JOBS</h1>
<p class="abs hero-sub">Lorem Ipsum is simply dummy text of the</p>
<a class="btn" href="#" style="left:523px;top:408px;width:158px;height:48px">READ MORE</a>
<div class="abs dots"><i></i><i></i><i class="on"></i><i></i><i></i></div>

<!-- WELCOME -->
<svg class="abs" style="left:0;top:600px" width="1200" height="650" viewBox="0 0 1200 650">
  <path d="M0 0L600 55 1200 0V580L600 640 0 580Z" fill="var(--soft)"/>
</svg>
<svg class="abs" style="left:130px;top:700px" width="480" height="480" viewBox="0 0 480 480" role="img" aria-label="Cluster of hexagon photographs of people working">
  <defs>
    <linearGradient id="ph1" x1="0" y1="0" x2="1" y2="1"><stop offset="0" stop-color="#d9b892"/><stop offset="1" stop-color="#8a6a52"/></linearGradient>
    <linearGradient id="ph2" x1="0" y1="0" x2="1" y2="1"><stop offset="0" stop-color="#7a8c98"/><stop offset="1" stop-color="#2c3540"/></linearGradient>
    <linearGradient id="ph3" x1="0" y1="0" x2="1" y2="1"><stop offset="0" stop-color="#c8c2bc"/><stop offset="1" stop-color="#5c5560"/></linearGradient>
  </defs>
  <polygon points="200,10 282,57 282,152 200,199 118,152 118,57" fill="url(#ph1)"/>
  <polygon points="118,152 200,199 200,294 118,341 36,294 36,199" fill="url(#ph2)"/>
  <polygon points="282,152 364,199 364,294 282,341 200,294 200,199" fill="url(#ph3)"/>
  <polygon points="200,294 282,341 282,436 200,470 118,436 118,341" fill="url(#ph2)"/>
  <polygon points="364,294 446,341 446,436 364,470 282,436 282,341" fill="url(#ph1)"/>
</svg>
<div class="abs welcome-text">
  <h3>WELCOME TO</h3>
  <h2>NOVEXA</h2>
  <p>But I must explain to you how all this mistaken idea of denouncing pleasure and praising pain was born and I will give you a complete account of the system, and expound the actual teachings of the great explorer of the truth, the master-builder of human happiness. No one rejects, dislikes, or avoids pleasure itself, because it is pleasure, but because those who do not know how to pursue pleasure rationally encounter consequences</p>
</div>
<a class="btn" href="#" style="left:653px;top:1057px;width:158px;height:48px">READ MORE</a>

<!-- SERVICES -->
<h2 class="section-title" style="top:1312px">OUR SERVICES</h2>
<svg class="abs" style="left:0;top:1440px" width="1200" height="180" viewBox="0 0 1200 180">
  <defs>
    <linearGradient id="ring" x1="0" y1="0" x2="1" y2="1"><stop offset="0" stop-color="var(--blue)"/><stop offset=".5" stop-color="var(--purple)"/><stop offset="1" stop-color="var(--pink)"/></linearGradient>
  </defs>
  <g fill="none" stroke="url(#ring)" stroke-width="5">
    <polygon points="233,5 307,47 307,133 233,175 159,133 159,47"/>
    <polygon points="475,5 549,47 549,133 475,175 401,133 401,47"/>
    <polygon points="722,5 796,47 796,133 722,175 648,133 648,47"/>
    <polygon points="964,5 1038,47 1038,133 964,175 890,133 890,47"/>
  </g>
  <path d="M233 100l-20-20a11 11 0 0120-10 11 11 0 0120 10z" fill="var(--pink)"/>
  <path d="M203 102c6 6 14 14 30 18 16-4 24-12 30-18" fill="none" stroke="var(--purple)" stroke-width="4"/>
  <rect x="448" y="62" width="54" height="38" rx="3" fill="none" stroke="var(--purple)" stroke-width="4"/>
  <rect x="465" y="100" width="20" height="10" fill="var(--purple)"/>
  <circle cx="475" cy="80" r="9" fill="var(--pink)"/>
  <rect x="694" y="60" width="56" height="42" fill="none" stroke="var(--purple)" stroke-width="4"/>
  <path d="M704 94l12-14 10 8 14-16" fill="none" stroke="var(--pink)" stroke-width="4"/>
  <rect x="944" y="56" width="40" height="52" fill="none" stroke="var(--purple)" stroke-width="4"/>
  <path d="M952 72h24M952 82h24M952 92h16" stroke="var(--pink)" stroke-width="3"/>
</svg>
<div class="service" style="left:133px"><h3>LOREM IPSUM</h3><p>Sed ut perspiciatis unde omnis iste natus error sit voluptatem accusantium doloremque laudantium, totam rem ape riam eaque ipsa.</p></div>
<div class="service" style="left:375px"><h3>LOREM IPSUM</h3><p>Sed ut perspiciatis unde omnis iste natus error sit voluptatem accusantium doloremque laudantium, totam rem ape riam eaque ipsa.</p></div>
<div class="service" style="left:622px"><h3>LOREM IPSUM</h3><p>Sed ut perspiciatis unde omnis iste natus error sit voluptatem accusantium doloremque laudantium, totam rem ape riam eaque ipsa.</p></div>
<div class="service" style="left:864px"><h3>LOREM IPSUM</h3><p>Sed ut perspiciatis unde omnis iste natus error sit voluptatem accusantium doloremque laudantium, totam rem ape riam eaque ipsa.</p></div>
<a class="btn small" href="#" style="left:189px;top:1795px">READ MORE</a>
<a class="btn small" href="#" style="left:431px;top:1795px">READ MORE</a>
<a class="btn small" href="#" style="left:678px;top:1795px">READ MORE</a>
<a class="btn small" href="#" style="left:920px;top:1795px">READ MORE</a>

<!-- BANNER -->
<svg class="abs" style="left:0;top:1913px" width="1200" height="520" viewBox="0 0 1200 520">
  <defs>
    <linearGradient id="band" x1="0" y1="0" x2="1" y2="0">
      <stop offset="0" stop-color="var(--deep)"/>
      <stop offset=".4" stop-color="var(--violet)"/>
      <stop offset=".65" stop-color="#c7b8d6"/>
      <stop offset="1" stop-color="#2d3d5c"/>
    </linearGradient>
  </defs>
  <path role="img" aria-label="Photograph of young women working at computers, blended into a purple gradient" d="M0 0H1200V460L600 405 0 480Z" fill="url(#band)"/>
</svg>
<div class="abs banner-text">
  <h2>Lorem ipsum dolor sit ametconsectetur adipiscing</h2>
  <p>Sed ut perspiciatis unde omnis iste natus error sit voluptatem accusantium doloremque laudantium, totam rem ape riam eaque ipsa.</p>
</div>
<a class="btn" href="#" style="left:160px;top:2268px;width:138px;height:44px;background:var(--red)">READ MORE</a>

<!-- JOBS -->
<svg class="abs" style="left:0;top:2380px" width="1200" height="705" viewBox="0 0 1200 705">
  <defs>
    <linearGradient id="hexring" x1="0" y1="0" x2="1" y2="1"><stop offset="0" stop-color="var(--violet)"/><stop offset=".5" stop-color="var(--purple)"/><stop offset="1" stop-color="var(--pink)"/></linearGradient>
    <linearGradient id="jobphoto" x1="0" y1="0" x2="1" y2="1"><stop offset="0" stop-color="#e6c27a"/><stop offset=".5" stop-color="#b58a60"/><stop offset="1" stop-color="#6f6a72"/></linearGradient>
  </defs>
  <rect x="0" y="60" width="1200" height="645" fill="var(--soft)"/>
  <path d="M0 100L600 30 1200 100V0H0Z" fill="var(--soft)"/>
  <polygon points="395,145 612,270 612,520 395,645 178,520 178,270" fill="url(#hexring)"/>
  <polygon points="395,175 586,285 586,505 395,615 204,505 204,285" fill="#fff"/>
  <polygon role="img" aria-label="Photograph of a young man helping an older man at a desk" points="395,200 565,298 565,492 395,590 225,492 225,298" fill="url(#jobphoto)"/>
</svg>
<div class="abs job-card">
  <span class="tag">JOBS</span>
  <h3>Lorem ipsum dolor sit ametconsect</h3>
  <p>At vero eos et accusamus et iusto odio dignissimos ducimus qui blanditiis praesentium voluptatum deleniti atque corrupti quos dolores et quas molestias excepturi sint occaecati cupiditate non provident, similique sunt in culpa qui officia deserunt mollitia animi, id est laborum et dolorum fuga.</p>
</div>
<a class="btn" href="#" style="left:662px;top:2894px;width:158px;height:48px">APPLY JOB</a>

<!-- BLOG -->
<h2 class="section-title" style="top:3156px">LATEST BLOG</h2>
<svg class="abs" style="left:60px;top:3280px" width="1100" height="290" viewBox="0 0 1100 290">
  <defs>
    <linearGradient id="bp1" x1="0" y1="0" x2="1" y2="1"><stop offset="0" stop-color="#9b8f86"/><stop offset="1" stop-color="#4a3e44"/></linearGradient>
    <linearGradient id="bp2" x1="0" y1="0" x2="1" y2="1"><stop offset="0" stop-color="#5f6b86"/><stop offset="1" stop-color="#c6c0a8"/></linearGradient>
  </defs>
  <path d="M32 116l-12 14 12 14" stroke="#888" stroke-width="3" fill="none"/>
  <path d="M1068 116l12 14-12 14" stroke="#888" stroke-width="3" fill="none"/>
  <polygon points="195,15 313,83 313,219 195,287 77,219 77,83" fill="url(#hexring)"/>
  <polygon role="img" aria-label="Photograph of a woman waiting in a row of chairs" points="195,30 300,91 300,211 195,272 90,211 90,91" fill="url(#bp1)"/>
  <polygon points="696,15 814,83 814,219 696,287 578,219 578,83" fill="url(#hexring)"/>
  <polygon role="img" aria-label="Photograph of a desk lamp and notes on a wall" points="696,30 801,91 801,211 696,272 591,211 591,91" fill="url(#bp2)"/>
</svg>
<article class="post" style="left:396px"><time>22 FEB, 2019</time><h3>Lorem ipsum dolor sit ame</h3><p>At vero eos et accusamus et iusto odio dignissimos ducimus qui blanditiis praesentium voluptatum deleniti atque corrupti quos.</p></article>
<a class="btn small" href="#" style="left:396px;top:3496px">READ MORE</a>
<article class="post" style="left:894px"><time>22 FEB, 2019</time><h3>Lorem ipsum dolor sit ame</h3><p>At vero eos et accusamus et iusto odio dignissimos ducimus qui blanditiis praesentium voluptatum deleniti atque corrupti quos.</p></article>
<a class="btn small" href="#" style="left:894px;top:3496px">READ MORE</a>

<!-- TESTIMONIALS -->
<div class="abs testimonials"></div>
<h2 class="section-title" style="top:3702px">TESTIMONIALS</h2>
<div class="abs qmark" style="left:318px;top:3772px">“</div>
<p class="abs quote">On the other hand, we denounce with righteous indignation and dislike men who are so beguiled and demoralized by the charms of pleasure of the moment so blinded by desire, that they cannot foresee the pain and trouble that are bound to ensue and equal blame belongs to those who fail in their duty through weakness of will, which is the same as saying through shrinking from toil and pain. These cases are perfectly simple and eas.</p>
<div class="abs qmark" style="left:738px;top:4022px">”</div>
<p class="abs author">DANIEL MARLOW</p>
<svg class="abs" style="left:195px;top:3880px" width="810" height="30" viewBox="0 0 810 30">
  <path d="M14 3L2 15l12 12M796 3l12 12-12 12" stroke="#999" stroke-width="3" fill="none"/>
</svg>

<!-- FOOTER -->
<svg class="abs" style="left:0;top:4130px" width="1200" height="404" viewBox="0 0 1200 404">
  <defs>
    <linearGradient id="foot" x1="0" y1="0" x2="0" y2="1"><stop offset="0" stop-color="#5a3596"/><stop offset="1" stop-color="var(--deep)"/></linearGradient>
  </defs>
  <path d="M0 60L600 10 1200 60V404H0Z" fill="url(#foot)"/>
  <path d="M0 60L600 10 1200 60" fill="none" stroke="var(--pink)" stroke-width="9"/>
</svg>
<div class="abs brand" style="left:148px;top:4318px;font-size:42px;display:flex;align-items:center;gap:14px"><span style="width:20px;height:20px;border-radius:50%;background:var(--pink)"></span>NOVEXA</div>
<div class="footer-col" style="left:490px">
  <h4>CONTACT US</h4>
  <ul>
    <li><svg width="12" height="16" viewBox="0 0 12 16"><path d="M6 0a6 6 0 00-6 6c0 4 6 10 6 10s6-6 6-10a6 6 0 00-6-6z" fill="#fff"/><circle cx="6" cy="6" r="2" fill="var(--deep)"/></svg><span>Lindenweg 24<br>4811 KB Veldhoven, The Netherlands</span></li>
    <li><svg width="12" height="12" viewBox="0 0 12 12"><path d="M2 0l3 3-1.5 1.5a7 7 0 004 4L9 7l3 3-2 2C5 12 0 7 0 2z" fill="#fff"/></svg><span>888.888.8888</span></li>
    <li><svg width="13" height="10" viewBox="0 0 13 10"><rect width="13" height="10" fill="#fff"/><path d="M0 0l6.5 5L13 0" stroke="var(--deep)" fill="none"/></svg><span>info@novexa.com</span></li>
  </ul>
</div>
<div class="footer-col menu" style="left:792px">
  <h4>MENU</h4>
  <ul><li>HOME</li><li>ABOUT US</li><li>SERVICES</li><li>JOBS</li><li>BLOG</li><li>CONTACT US</li></ul>
</div>
<div class="footer-col social" style="left:944px">
  <h4>CONNECT WITH US</h4>
  <ul><li><span class="ico"></span>Community</li><li><span class="ico"></span>Updates</li><li><span class="ico"></span>Network</li></ul>
</div>
<p class="abs copyright">Copyright @ 2019 All Rights Reserved</p>

</body>
</html>
```